Veltrane Group Business Card Design

The CEO is looking for a new trendy look for his business card.
You can stay with current branding or come up with something new/creative. It can be 3D, including Medical Office buildings. You can use our logo in a variety of colors. Please include name, title, company name, company website, email address, cell number

Target Market(s)

Real Estate Development and Construction

Industry/Entity Type

Health care real estate

Contact Information for Business Card

Rohesh Kamdar, CEO M-604.781.2249 E-roheshkamdar@veltrane.com Address:4180 Lindqvist Ave, Tampa, FL 33482 www.veltrane.com

Font styles to use
Other font styles liked:
• Be creative

Requirements
Must have
• Creative, trendy look
Nice to have
• Please go to our website to get a feel- www. veltrane.com
Should not have
• small fonts

```html
<!DOCTYPE html>
<html lang="en">
<head>
<meta charset="UTF-8">
<title>Veltrane Group Business Card</title>
<link rel="stylesheet" href="https://fonts.googleapis.com/css2?family=Poppins:wght@400;600;700;800&display=swap">
<style>
  :root {
    --navy: #1e3153;
    --navy-light: #3a5585;
    --red: #b41f2a;
    --paper: #dedede;
    --white: #ffffff;
    --stage: #1b1b1b;
  }
  * { box-sizing: border-box; margin: 0; padding: 0; }
  html, body {
    width: 1200px;
    height: 900px;
    overflow: hidden;
    background: var(--stage);
    font-family: "Poppins", sans-serif;
  }
  .stage {
    width: 1200px;
    height: 900px;
    display: flex;
    flex-direction: column;
    align-items: center;
    justify-content: center;
    gap: 40px;
  }
  .card {
    width: 640px;
    height: 366px;
    position: relative;
    overflow: hidden;
  }

  /* Back side */
  .card-back {
    background: var(--navy);
    display: flex;
    align-items: center;
    justify-content: center;
  }
  .card-back .wordmark {
    color: var(--navy-light);
    font-size: 60px;
    font-weight: 800;
    letter-spacing: -1px;
  }

  /* Front side */
  .card-front { background: var(--paper); }
  .front-top {
    position: absolute;
    inset: 0 0 auto 0;
    height: 170px;
    display: flex;
    align-items: center;
    justify-content: center;
    padding-left: 60px;
  }
  .front-top .wordmark {
    color: var(--red);
    font-size: 60px;
    font-weight: 800;
    letter-spacing: -1px;
  }
  .contact-band {
    position: absolute;
    left: 0; right: 0;
    top: 170px;
    height: 122px;
    background: var(--navy);
    display: flex;
    align-items: center;
    color: var(--white);
  }
  .person {
    width: 262px;
    text-align: right;
    padding-right: 22px;
  }
  .person-name {
    font-size: 21px;
    font-weight: 700;
    letter-spacing: 1px;
    text-transform: uppercase;
    line-height: 1.2;
  }
  .person-title {
    font-size: 17px;
    font-weight: 400;
    letter-spacing: 1px;
  }
  .divider {
    width: 1.5px;
    height: 78px;
    background: var(--white);
  }
  .contact-list {
    list-style: none;
    padding-left: 22px;
    font-size: 16px;
    line-height: 1.6;
  }
  .contact-list li {
    display: flex;
    align-items: center;
    gap: 10px;
  }
  .contact-list svg {
    width: 16px;
    height: 16px;
    flex: none;
  }
  .address-band {
    position: absolute;
    left: 0; right: 0; bottom: 0;
    height: 74px;
    background: var(--red);
    color: var(--white);
    font-size: 18px;
    display: flex;
    align-items: center;
    padding-left: 120px;
  }
</style>
</head>
<body>
<main class="stage">
  <section class="card card-back">
    <span class="wordmark">Veltrane Group</span>
  </section>

  <section class="card card-front">
    <div class="front-top">
      <span class="wordmark">Veltrane Group</span>
    </div>

    <div class="contact-band">
      <div class="person">
        <p class="person-name">Rohesh Kamdar</p>
        <p class="person-title">CEO</p>
      </div>
      <div class="divider"></div>
      <ul class="contact-list">
        <li>
          <svg viewBox="0 0 24 24" fill="none" stroke="currentColor" stroke-width="2" stroke-linejoin="round"><path d="M5 3h4l2 5-2.5 1.5a11 11 0 0 0 6 6L16 13l5 2v4a2 2 0 0 1-2 2A16 16 0 0 1 3 5a2 2 0 0 1 2-2z"/></svg>
          604.781.2249
        </li>
        <li>
          <svg viewBox="0 0 24 24" fill="none" stroke="currentColor" stroke-width="2"><rect x="2" y="5" width="20" height="14"/><path d="M2 5l10 8 10-8"/></svg>
          roheshkamdar@veltrane.com
        </li>
        <li>
          <svg viewBox="0 0 24 24" fill="none" stroke="currentColor" stroke-width="2"><circle cx="12" cy="12" r="10"/><path d="M2 12h20M12 2c3 3 3 17 0 20M12 2c-3 3-3 17 0 20"/></svg>
          www.veltrane.com
        </li>
      </ul>
    </div>

    <div class="address-band">4180 Lindqvist Ave, Tampa, FL 33482</div>
  </section>
</main>
</body>
</html>
```